Lanternfield Drinks business cards

We need a business card design for our new logo. The company is modern, progressive, professional, yet approachable. The key products are ready to drink bottles and cans of coffee based beverages.
These cards will be a critical part of the first impression made by our sales organization, business development team, and all external facing personnel.
Card can be a vertical or horizontal orientation.

Target Market(s)

Customers, suppliers, business partners

Industry/Entity Type

Business

Contact Information for Business Card

Business cards should feature Company Name and Logo.

Font styles to use
Serif

Colors

Designer to choose colors to be used in the design.

Requirements
Must have
• Strong readability of Name, phone #, mobile number and email address.
• Job title, website url, Street Address, and other details can be secondary level readability.
Nice to have
• High impact, simplistic quality design.
• Ok to utilize the 'H in the box' separate from the company name

```html
<!DOCTYPE html>
<html lang="en">
<head>
<meta charset="utf-8">
<title>Lanternfield Drinks – Business Cards</title>
<link rel="stylesheet" href="https://fonts.googleapis.com/css2?family=Cinzel:wght@600;700&family=PT+Sans:wght@400&display=swap">
<style>
  :root{
    --bg:#ece9e6;
    --white:#ffffff;
    --orange:#f05a2b;
    --amber:#f7941d;
    --orange-deep:#ef5a24;
    --orange-light:#f89a2a;
    --ink-light:#ffffff;
  }
  *{margin:0;padding:0;box-sizing:border-box}
  html,body{width:1200px;height:900px;overflow:hidden;background:var(--bg)}
  .canvas{position:relative;width:1200px;height:900px}

  .card{position:absolute;overflow:hidden;box-shadow:0 6px 18px rgba(0,0,0,.18)}

  /* Front */
  .card-front{left:78px;top:33px;width:588px;height:364px;background:var(--white)}
  .card-front .bands{position:absolute;left:0;top:0}
  .brand{position:absolute;left:90px;top:45px;display:flex;align-items:center;gap:16px}
  .brand-square{width:64px;height:64px;background:var(--orange)}
  .brand-name{font-family:"Cinzel",serif;font-weight:700;font-size:34px;line-height:38px;color:var(--orange);letter-spacing:.5px}

  .contacts{position:absolute;left:30px;top:256px;list-style:none;font-family:"PT Sans",sans-serif;font-size:15px;color:var(--ink-light)}
  .contacts li{display:flex;align-items:center;height:21.5px;gap:8px}
  .contacts svg{width:13px;height:13px;flex:none}

  .person{position:absolute;right:36px;top:244px;text-align:right;color:var(--ink-light);font-family:"PT Sans",sans-serif}
  .person-name{font-family:"Cinzel",serif;font-weight:600;font-size:19px;line-height:22px;letter-spacing:.5px}
  .person-title{font-size:15px;line-height:20px}
  .person-address{margin-top:10px;font-size:15px;line-height:21px}

  /* Back */
  .card-back{left:388px;top:505px;width:567px;height:352px}
  .card-back .surface{position:absolute;inset:0;background:radial-gradient(ellipse at 50% 45%,var(--orange-light) 0%,var(--orange-deep) 75%)}
  .back-name{position:absolute;left:0;right:0;top:118px;text-align:center;font-family:"Cinzel",serif;font-weight:700;font-size:44px;line-height:48px;color:var(--white);letter-spacing:1px}
  .back-web{position:absolute;left:0;right:0;top:294px;text-align:center;font-family:"PT Sans",sans-serif;font-size:16px;letter-spacing:1.5px;color:var(--white)}
</style>
</head>
<body>
<main class="canvas">

  <section class="card card-front" aria-label="Business card front">
    <svg class="bands" width="588" height="364" viewBox="0 0 588 364" aria-hidden="true">
      <polygon fill="var(--orange)" points="414,180 588,180 588,364 0,364 0,218 378,218"/>
      <polygon fill="var(--amber)" points="0,191 392,191 374,214 0,214"/>
    </svg>

    <div class="brand">
      <div class="brand-square"></div>
      <div class="brand-name">Lanternfield<br>Drinks</div>
    </div>

    <ul class="contacts">
      <li>
        <svg viewBox="0 0 13 13"><rect x="3" y="0.5" width="7" height="12" rx="1.2" fill="none" stroke="#fff" stroke-width="1.4"/><rect x="5" y="10" width="3" height="1" fill="#fff"/></svg>
        044-310 482 975
      </li>
      <li>
        <svg viewBox="0 0 13 13"><path d="M1 4 Q6.5 0 12 4 L10.5 5.5 L8.5 4.5 L8.5 3.5 Q6.5 3 4.5 3.5 L4.5 4.5 L2.5 5.5 Z" fill="#fff"/><rect x="3" y="6" width="7" height="5.5" rx="1" fill="#fff"/></svg>
        044-310 482 975
      </li>
      <li>
        <svg viewBox="0 0 13 13"><rect x="0.5" y="2.5" width="12" height="8" fill="#fff"/><path d="M0.5 2.5 L6.5 7 L12.5 2.5" fill="none" stroke="var(--orange)" stroke-width="1"/></svg>
        hello@lanternfield.com
      </li>
      <li>
        <svg viewBox="0 0 13 13"><circle cx="6.5" cy="6.5" r="6" fill="#fff"/><path d="M4 3.5 Q6 5 5 7 Q7 8 6.5 10.5 M8.5 2.5 Q9 4.5 10.5 5" fill="none" stroke="var(--orange)" stroke-width="1.2"/></svg>
        www.lanternfield.com
      </li>
    </ul>

    <div class="person">
      <p class="person-name">Marcus Bellamy</p>
      <p class="person-title">Managing Director</p>
      <p class="person-address">48 Copperleaf Avenue<br>Northvale, 204517</p>
    </div>
  </section>

  <section class="card card-back" aria-label="Business card back">
    <div class="surface" role="img" aria-label="Orange gradient background with a faint repeating brand monogram pattern"></div>
    <p class="back-name">Lanternfield<br>Drinks</p>
    <p class="back-web">www.lanternfield.com</p>
  </section>

</main>
</body>
</html>
```